Working Capital graphics

Our business advisory firm requires 9 images to be re-created and improved in the branding of our business.

The 9 images have been uploaded below and the colours and branding of the business can be found at the website www.tallowmereadvisory.com.au

```html
<!DOCTYPE html>
<html lang="en">
<head>
<meta charset="utf-8">
<title>Working Capital Graphics</title>
<link href="https://fonts.googleapis.com/css2?family=Montserrat:ital,wght@0,600;0,700;0,800;1,700&display=swap" rel="stylesheet">
<style>
  :root{
    --navy:#0f2a66;
    --blue:#1a4ab5;
    --mid:#1f86d8;
    --cyan:#0db0f0;
    --sky:#5fc8f5;
    --orange:#f7931e;
    --ink:#123a8c;
    --bg:#f4f4f4;
    --panel:#ffffff;
  }
  html,body{margin:0;padding:0;width:1200px;height:1088px;overflow:hidden;background:var(--bg);}
  .board{display:block;width:1200px;height:1088px;font-family:"Montserrat",sans-serif;}
  .panel{fill:var(--panel);}
  .lbl{fill:var(--ink);font-weight:700;font-size:9px;text-anchor:middle;}
  .lbl-sm{fill:var(--ink);font-weight:700;font-size:7px;text-anchor:middle;}
  .lbl-xs{fill:var(--ink);font-weight:700;font-size:6px;text-anchor:middle;}
  .legend-text{fill:var(--ink);font-weight:700;font-size:6px;text-anchor:start;}
  .title-cy{fill:var(--cyan);font-weight:700;font-size:14px;text-anchor:middle;}
  .head{fill:var(--ink);font-weight:700;font-size:15px;}
  .head-sm{fill:var(--ink);font-weight:700;font-size:12px;text-anchor:middle;}
  .w{fill:#fff;font-weight:700;text-anchor:middle;}
  .ring-label{fill:#fff;font-weight:700;text-anchor:middle;}
  .arr{stroke:var(--orange);stroke-width:1.6;fill:none;marker-end:url(#ahO);}
  .box-o{fill:#fff;stroke:var(--orange);stroke-width:2;}
  .box-c{fill:#fff;stroke:var(--cyan);stroke-width:1.6;}
  .tree{stroke:var(--cyan);stroke-width:1.5;fill:none;}
  .axis{stroke:var(--cyan);stroke-width:2;fill:none;}
  .num{fill:var(--ink);font-weight:700;font-size:17px;}
  .big{fill:var(--ink);font-weight:700;font-size:20px;}
  .ring-seg{fill:none;stroke-width:46;}
  .sat{fill:#fff;stroke:var(--cyan);stroke-width:3;}
  .sat-arc{fill:none;stroke:var(--orange);stroke-width:3;}
</style>
</head>
<body>
<svg class="board" viewBox="0 0 1944 1763" xmlns="http://www.w3.org/2000/svg">
  <defs>
    <marker id="ahO" viewBox="0 0 10 10" refX="8" refY="5" markerWidth="5" markerHeight="5" orient="auto"><path d="M0 0L10 5L0 10Z" fill="#f7931e"/></marker>
    <marker id="ahC" viewBox="0 0 10 10" refX="8" refY="5" markerWidth="6" markerHeight="6" orient="auto"><path d="M0 0L10 5L0 10Z" fill="#0db0f0"/></marker>
    <marker id="ahN" viewBox="0 0 10 10" refX="6" refY="5" markerWidth="5" markerHeight="5" orient="auto"><path d="M0 0L10 5L0 10Z" fill="#1a3a8f"/></marker>
    <path id="ringTop" d="M968 436A118 118 0 1 1 968 200A118 118 0 1 1 968 436"/>
    <path id="ringBot" d="M968 200A118 118 0 1 0 968 436A118 118 0 1 0 968 200"/>
  </defs>

  <rect x="0" y="0" width="1944" height="1763" fill="#f4f4f4"/>

  <!-- ============ Panel 1 : cycles ============ -->
  <g class="cycles">
    <rect class="panel" x="31" y="49" width="612" height="538"/>
    <text class="title-cy"><tspan x="193" y="173">REVENUE</tspan><tspan x="193" y="190">MANAGEMENT</tspan></text>
    <text class="lbl-sm"><tspan x="122" y="102">CASH</tspan><tspan x="122" y="112">MANAGEMENT</tspan></text>
    <text class="lbl-sm"><tspan x="193" y="90">CUSTOMER</tspan><tspan x="193" y="100">STRATEGY</tspan></text>
    <text class="lbl-sm"><tspan x="267" y="95">SALES</tspan><tspan x="267" y="105">MANAGEMENT</tspan></text>
    <text class="lbl"><tspan x="280" y="123">RISK</tspan><tspan x="280" y="134">MANAGEMENT</tspan></text>
    <text class="lbl-sm"><tspan x="303" y="161">CONTRACT</tspan><tspan x="303" y="171">MANAGEMENT</tspan></text>
    <text class="lbl-sm"><tspan x="295" y="202">SALES ORDER</tspan><tspan x="295" y="212">PROCESSING</tspan></text>
    <text class="lbl-sm"><tspan x="258" y="240">CREDIT</tspan><tspan x="258" y="250">CHECK</tspan></text>
    <text class="lbl-sm"><tspan x="199" y="254">ORDER</tspan><tspan x="199" y="264">FULFILLMENT</tspan></text>
    <text class="lbl-sm" x="134" y="254">BILLING</text>
    <text class="lbl-sm"><tspan x="104" y="222">CUSTOMER</tspan><tspan x="104" y="232">SERVICE</tspan></text>
    <text class="lbl-xs"><tspan x="91" y="180">CASH</tspan><tspan x="91" y="189">COLLECTION</tspan></text>
    <text class="lbl-xs"><tspan x="98" y="136">RECEIPT &amp;</tspan><tspan x="98" y="146">ALLOCATION</tspan><tspan x="98" y="156">OF CASH</tspan></text>
    <path class="arr" d="M155 101L168 97"/><path class="arr" d="M218 97L230 101"/>
    <path class="arr" d="M248 110L256 117"/><path class="arr" d="M271 145L274 156"/>
    <path class="arr" d="M277 176L277 188"/><path class="arr" d="M270 217L263 228"/>
    <path class="arr" d="M240 245L228 252"/><path class="arr" d="M168 256L155 253"/>
    <path class="arr" d="M118 248L110 238"/><path class="arr" d="M100 212L96 197"/>
    <path class="arr" d="M108 168L109 162"/><path class="arr" d="M124 128L132 118"/>
    <rect class="box-o" x="141" y="273" width="100" height="17" stroke-width="1.6"/>
    <text class="lbl-sm" x="191" y="285">CUSTOMER TO CASH</text>
    <path d="M258 318L340 238L420 318Z" fill="var(--cyan)"/>
    <path d="M340 238L340 296M300 278L340 296L380 278" stroke="#fff" stroke-width="1.5" fill="none"/>
    <text class="w" font-size="9" transform="translate(312 283) rotate(-45)">A/R</text>
    <text class="w" font-size="7" transform="translate(358 279) rotate(45)">INVENTORY</text>
    <text class="w" font-size="9" x="340" y="310">A/P</text>
    <path class="arr" d="M298 270L286 258"/><path class="arr" d="M382 270L394 258"/>
    <path class="arr" d="M341 326L341 342"/>
    <text class="title-cy"><tspan x="484" y="165">SUPPLY CHAIN</tspan><tspan x="484" y="181">MANAGEMENT</tspan></text>
    <text class="lbl-xs"><tspan x="483" y="88">PURCHASING</tspan><tspan x="483" y="97">STRATEGY</tspan></text>
    <text class="lbl-sm"><tspan x="555" y="99">RISK</tspan><tspan x="555" y="110">MANAGEMENT</tspan></text>
    <text class="lbl-xs"><tspan x="581" y="133">CONTRACT</tspan><tspan x="581" y="142">MANAGEMENT</tspan></text>
    <text class="lbl-xs"><tspan x="587" y="175">SALES ORDER</tspan><tspan x="587" y="185">PROCESSING</tspan></text>
    <text class="lbl-sm"><tspan x="559" y="217">CREDIT</tspan><tspan x="559" y="228">CHECK</tspan></text>
    <text class="lbl-sm"><tspan x="487" y="241">SALES ORDER</tspan><tspan x="487" y="252">PROCESSING</tspan></text>
    <text class="lbl-sm"><tspan x="417" y="214">RISK</tspan><tspan x="417" y="225">MANAGEMENT</tspan></text>
    <text class="lbl"><tspan x="383" y="170">CASH</tspan><tspan x="383" y="181">COLLECTION</tspan></text>
    <text class="lbl-sm" x="387" y="146">WAREHOUSING</text>
    <text class="lbl-sm" x="416" y="112">DRISTIBUTION</text>
    <path class="arr" d="M446 98L458 93"/><path class="arr" d="M508 93L519 98"/>
    <path class="arr" d="M546 118L552 128"/><path class="arr" d="M564 148L566 161"/>
    <path class="arr" d="M563 190L560 203"/><path class="arr" d="M537 233L525 240"/>
    <path class="arr" d="M450 241L438 235"/><path class="arr" d="M402 205L395 194"/>
    <path class="arr" d="M402 160L404 152"/><path class="arr" d="M412 132L417 122"/>
    <rect class="box-o" x="427" y="268" width="120" height="17" stroke-width="1.6"/>
    <text class="lbl-sm" x="487" y="280">FORECAST TO FULFILLMENT</text>
    <text class="title-cy"><tspan x="343" y="431">EXPENDITURE</tspan><tspan x="343" y="447">MANAGEMENT</tspan></text>
    <text class="lbl"><tspan x="342" y="358">PURCHASING</tspan><tspan x="342" y="370">STRATEGY</tspan></text>
    <text class="lbl"><tspan x="413" y="381">CASH</tspan><tspan x="413" y="392">MANAGEMENT</tspan></text>
    <text class="lbl"><tspan x="444" y="416">CUSTOMER</tspan><tspan x="444" y="428">SERVICE</tspan></text>
    <text class="lbl"><tspan x="440" y="459">CUSTOMER</tspan><tspan x="440" y="470">SERVICE</tspan></text>
    <text class="lbl"><tspan x="421" y="490">CASH</tspan><tspan x="421" y="502">COLLECTION</tspan></text>
    <text class="lbl"><tspan x="340" y="510">CASH</tspan><tspan x="340" y="522">COLLECTION</tspan></text>
    <text class="lbl"><tspan x="264" y="492">RISK</tspan><tspan x="264" y="503">MANAGEMENT</tspan></text>
    <text class="lbl"><tspan x="242" y="458">CUSTOMER</tspan><tspan x="242" y="470">SERVICE</tspan></text>
    <text class="lbl"><tspan x="238" y="414">CASH</tspan><tspan x="238" y="425">COLLECTION</tspan></text>
    <text class="lbl"><tspan x="272" y="376">CASH</tspan><tspan x="272" y="387">MANAGEMENT</tspan></text>
    <path class="arr" d="M296 368L308 362"/><path class="arr" d="M378 364L392 372"/>
    <path class="arr" d="M410 398L414 408"/><path class="arr" d="M421 433L420 445"/>
    <path class="arr" d="M412 474L407 483"/><path class="arr" d="M385 503L374 509"/>
    <path class="arr" d="M310 512L298 505"/><path class="arr" d="M272 478L267 468"/>
    <path class="arr" d="M259 445L260 430"/><path class="arr" d="M266 407L270 395"/>
    <rect class="box-o" x="289" y="536" width="98" height="17" stroke-width="1.6"/>
    <text class="lbl-sm" x="338" y="548">PURCHASE TO PAY</text>
  </g>

  <!-- ============ Panel 2 : ring ============ -->
  <g class="sales-ring">
    <rect class="panel" x="665" y="49" width="613" height="538"/>
    <circle cx="968" cy="318" r="162" fill="none" stroke="var(--blue)" stroke-width="1.5"/>
    <path class="ring-seg" stroke="var(--sky)" d="M863.8 262.6A118 118 0 0 1 923.8 208.6"/>
    <path class="ring-seg" stroke="#2aa6ec" d="M927.6 207.1A118 118 0 0 1 984.4 201.2"/>
    <path class="ring-seg" stroke="#1e9be0" d="M988.5 201.8A118 118 0 0 1 1065.8 252"/>
    <path class="ring-seg" stroke="var(--orange)" d="M1068.1 255.5A118 118 0 0 1 1055.7 397"/>
    <path class="ring-seg" stroke="#0d2657" d="M1052.8 400A118 118 0 0 1 920 425.8"/>
    <path class="ring-seg" stroke="#1a3f9a" d="M916.3 424.1A118 118 0 0 1 851.2 334.4"/>
    <path class="ring-seg" stroke="#1d4fc0" d="M850.6 330.4A118 118 0 0 1 861.9 266.3"/>
    <g class="ring-label">
      <text font-size="7" dy="-2"><textPath href="#ringTop" startOffset="284">CASH</textPath></text>
      <text font-size="7" dy="7"><textPath href="#ringTop" startOffset="284">SHORTFALL</textPath></text>
      <text font-size="10" dy="3"><textPath href="#ringTop" startOffset="355">0$</textPath></text>
      <text font-size="9" dy="3"><textPath href="#ringTop" startOffset="439">COST OF SALES</textPath></text>
      <text font-size="7.5" dy="-2"><textPath href="#ringTop" startOffset="566">OPERATING EXPENSES</textPath></text>
      <text font-size="7.5" dy="8"><textPath href="#ringTop" startOffset="566">FIXED COSTS</textPath></text>
      <text font-size="7.5" dy="3"><textPath href="#ringBot" startOffset="393">DIVIDENDS · INTEREST · TAX</textPath></text>
      <text font-size="7" dy="-2"><textPath href="#ringBot" startOffset="260">AP DAYS · AR DAYS</textPath></text>
      <text font-size="7" dy="7"><textPath href="#ringBot" startOffset="260">INV DAYS</textPath></text>
      <text font-size="7" dy="-2"><textPath href="#ringTop" startOffset="206">ADDITIONAL</textPath></text>
      <text font-size="7" dy="7"><textPath href="#ringTop" startOffset="206">DEBT</textPath></text>
    </g>
    <text fill="var(--orange)" font-weight="800" font-size="21" text-anchor="middle"><tspan x="972" y="310">NEXT $100 OF</tspan><tspan x="972" y="337">SALES VOLUME</tspan></text>
    <g fill="#fff" stroke-width="1.5">
      <path d="M968 131V153M1142 243L1120 252M1138 405L1116 393M977 508V484M805 398L822 388M812 233L828 242" stroke="var(--blue)"/>
      <circle cx="968" cy="103" r="28" stroke="var(--orange)"/>
      <circle cx="1166" cy="227" r="28" stroke="var(--orange)"/>
      <circle cx="1159" cy="424" r="28" stroke="var(--cyan)"/>
      <circle cx="977" cy="531" r="28" stroke="var(--orange)"/>
      <circle cx="777" cy="405" r="28" stroke="var(--orange)"/>
      <circle cx="783" cy="218" r="28" stroke="var(--orange)"/>
    </g>
    <g fill="var(--cyan)"><circle cx="968" cy="155" r="3"/><circle cx="1123" cy="245" r="3"/><circle cx="1118" cy="398" r="3"/><circle cx="977" cy="482" r="3"/><circle cx="822" cy="387" r="3"/><circle cx="826" cy="243" r="3"/></g>
    <text class="lbl-xs"><tspan x="968" y="101">REVENUE</tspan><tspan x="968" y="110">0$</tspan></text>
    <text class="lbl-xs"><tspan x="1166" y="222">GROSS</tspan><tspan x="1166" y="230">MARGINS</tspan><tspan x="1166" y="239">0$</tspan></text>
    <text class="lbl-xs"><tspan x="1159" y="422">EBIT</tspan><tspan x="1159" y="431">0$</tspan></text>
    <text class="lbl-xs" font-size="5.5"><tspan x="977" y="527">RETAINED</tspan><tspan x="977" y="535">INCOME</tspan><tspan x="977" y="543">0$</tspan></text>
    <text class="lbl-xs" font-size="5.5"><tspan x="777" y="397">AFTER</tspan><tspan x="777" y="404">WORKING</tspan><tspan x="777" y="411">CAPITAL</tspan><tspan x="777" y="418">0$</tspan></text>
    <text class="lbl-xs" font-size="5.5"><tspan x="783" y="209">AFTER</tspan><tspan x="783" y="216">ADDITIONAL</tspan><tspan x="783" y="223">FUNDING</tspan><tspan x="783" y="230">0$</tspan></text>
  </g>

  <!-- ============ Panel 3 : inventories ============ -->
  <g class="inventories">
    <rect class="panel" x="1303" y="49" width="612" height="538"/>
    <text class="head" x="1346" y="133">INVENTORIES</text>
    <text class="head-sm" x="1589" y="133">DRIVER GROUP</text>
    <text class="head-sm" x="1778" y="133">SUB-GROUP</text>
    <rect class="box-o" x="1340" y="293" width="116" height="60"/>
    <text class="head-sm"><tspan x="1398" y="319">INVENTORY</tspan><tspan x="1398" y="334">DRIVERS</tspan></text>
    <path class="tree" d="M1456 323H1498M1498 207V482M1498 207H1515M1498 308H1515M1498 393H1515M1498 482H1515"/>
    <path class="tree" d="M1647 207H1664M1664 162V249M1664 162H1684M1664 191H1684M1664 220H1684M1664 249H1684
      M1647 308H1664M1664 278V336M1664 278H1684M1664 307H1684M1664 336H1684
      M1647 393H1664M1664 365V418M1664 365H1684M1664 392H1684M1664 418H1684
      M1647 482H1664M1664 452V510M1664 452H1684M1664 481H1684M1664 510H1684"/>
    <g>
      <rect class="box-o" x="1540" y="194" width="107" height="26" stroke-width="1.5"/>
      <rect class="box-o" x="1540" y="295" width="107" height="26" stroke-width="1.5"/>
      <rect class="box-o" x="1540" y="380" width="107" height="26" stroke-width="1.5"/>
      <rect class="box-o" x="1540" y="469" width="107" height="26" stroke-width="1.5"/>
      <g fill="var(--cyan)" stroke="#fff" stroke-width="2"><circle cx="1527" cy="207" r="15"/><circle cx="1527" cy="308" r="15"/><circle cx="1527" cy="393" r="15"/><circle cx="1527" cy="482" r="15"/></g>
      <g class="w" font-size="14"><text x="1527" y="212">10</text><text x="1527" y="313">11</text><text x="1527" y="398">12</text><text x="1527" y="487">13</text></g>
      <g fill="var(--ink)" font-weight="700" font-style="italic" font-size="9" text-anchor="middle"><text x="1589" y="210">LOREM IPSUM</text><text x="1589" y="311">LOREM IPSUM</text><text x="1589" y="396">LOREM IPSUM</text><text x="1589" y="485">LOREM IPSUM</text></g>
    </g>
    <g>
      <rect class="box-c" x="1684" y="154" width="189" height="16"/><rect class="box-c" x="1684" y="183" width="189" height="16"/>
      <rect class="box-c" x="1684" y="212" width="189" height="16"/><rect class="box-c" x="1684" y="241" width="189" height="16"/>
      <rect class="box-c" x="1684" y="270" width="189" height="16"/><rect class="box-c" x="1684" y="299" width="189" height="16"/>
      <rect class="box-c" x="1684" y="328" width="189" height="16"/><rect class="box-c" x="1684" y="357" width="189" height="16"/>
      <rect class="box-c" x="1684" y="384" width="189" height="16"/><rect class="box-c" x="1684" y="410" width="189" height="16"/>
      <rect class="box-c" x="1684" y="444" width="189" height="16"/><rect class="box-c" x="1684" y="473" width="189" height="16"/>
      <rect class="box-c" x="1684" y="502" width="189" height="16"/>
    </g>
    <g class="lbl-sm">
      <text x="1778" y="165">LOREM IPSUM</text><text x="1778" y="194">LOREM IPSUM</text><text x="1778" y="223">LOREM IPSUM</text><text x="1778" y="252">LOREM IPSUM</text>
      <text x="1778" y="281">LOREM IPSUM</text><text x="1778" y="310">LOREM IPSUM</text><text x="1778" y="339">LOREM IPSUM</text><text x="1778" y="368">LOREM IPSUM</text>
      <text x="1778" y="395">LOREM IPSUM</text><text x="1778" y="421">LOREM IPSUM</text><text x="1778" y="455">LOREM IPSUM</text><text x="1778" y="484">LOREM IPSUM</text>
      <text x="1778" y="513">LOREM IPSUM</text>
    </g>
  </g>

  <!-- ============ Panel 4 : NWC chart ============ -->
  <g class="nwc-chart">
    <rect class="panel" x="29" y="616" width="612" height="538"/>
    <text fill="var(--ink)" font-weight="700" font-style="italic" font-size="13" x="115" y="670">NET WORKING CAPITAL ABSORPTION</text>
    <g class="num">
      <text x="117" y="712">450m</text><text x="117" y="761">450m</text><text x="117" y="809">450m</text><text x="117" y="858">450m</text>
      <text x="117" y="906">450m</text><text x="117" y="955">450m</text><text x="117" y="1004">450m</text><text x="117" y="1053">450m</text>
    </g>
    <g class="num" text-anchor="middle">
      <text x="207" y="1088">20m</text><text x="266" y="1088">20m</text><text x="324" y="1088">20m</text>
      <text x="382" y="1088">20m</text><text x="441" y="1088">20m</text><text x="499" y="1088">20m</text>
    </g>
    <text class="head-sm" font-size="13" x="358" y="1116">NET WORKING CAPITAL (NWC)</text>
    <path class="axis" d="M176 695V1065H537"/>
    <path d="M176 877H359M359 877V1065" stroke="var(--cyan)" stroke-width="1.5" stroke-dasharray="5 4"/>
    <path d="M355 877V762A115 115 0 1 0 474 877Z" fill="var(--orange)"/>
    <path d="M359 877L290 808M359 877L273 953M359 877L440 960" stroke="#fff" stroke-width="3"/>
    <g stroke="var(--cyan)" stroke-width="1.8" marker-end="url(#ahC)">
      <path d="M359 877L271 781"/><path d="M359 877V730"/><path d="M359 877L437 763"/>
      <path d="M359 877H496"/><path d="M359 877L443 974"/><path d="M359 877L251 966"/>
    </g>
    <circle cx="359" cy="877" r="9" fill="var(--cyan)" stroke="#fff" stroke-width="2"/>
    <g class="big" font-weight="800">
      <text x="252" y="774">A</text><text x="358" y="719">B</text><text x="433" y="751">C</text>
      <text x="491" y="869">D</text><text x="453" y="980">E</text><text x="233" y="982">F</text>
    </g>
    <g fill="var(--ink)" font-weight="700" font-size="14">
      <text x="207" y="746">LOREM IPSUM</text><text x="460" y="746">LOREM IPSUM</text>
      <text x="521" y="855">LOREM</text><text x="521" y="873">IPSUM</text>
      <text x="481" y="980">LOREM IPSUM</text><text x="227" y="1009">LOREM IPSUM</text>
    </g>
  </g>

  <!-- ============ Panel 5 : payables ============ -->
  <g class="payables">
    <rect class="panel" x="664" y="616" width="612" height="538"/>
    <text class="head" x="738" y="750">PAYABLES</text>
    <text class="head" x="1040" y="750">DRIVERS</text>
    <rect class="box-o" x="711" y="867" width="136" height="71"/>
    <text class="head-sm" font-size="14"><tspan x="779" y="898">PAYABLES</tspan><tspan x="779" y="917">DRIVERS</tspan></text>
    <path class="tree" d="M847 903H880M880 788V1015M880 788H893M880 847H893M880 903H893M880 958H893M880 1015H893"/>
    <g>
      <rect class="box-o" x="893" y="772" width="336" height="32"/><rect class="box-o" x="893" y="831" width="336" height="32"/>
      <rect class="box-o" x="893" y="887" width="336" height="32"/><rect class="box-o" x="893" y="942" width="336" height="32"/>
      <rect class="box-o" x="893" y="999" width="336" height="32"/>
      <g fill="var(--cyan)" stroke="#fff" stroke-width="2"><circle cx="910" cy="788" r="18"/><circle cx="910" cy="847" r="18"/><circle cx="910" cy="903" r="18"/><circle cx="910" cy="958" r="18"/><circle cx="910" cy="1015" r="18"/></g>
      <g class="w" font-size="17"><text x="910" y="794">14</text><text x="910" y="853">15</text><text x="910" y="909">16</text><text x="910" y="964">17</text><text x="910" y="1021">18</text></g>
      <g class="head-sm" font-size="11"><text x="1073" y="792">LOREM IPSUM DOLOR SIT</text><text x="1073" y="851">LOREM IPSUM DOLOR SIT</text><text x="1073" y="907">LOREM IPSUM DOLOR SIT</text><text x="1073" y="962">LOREM IPSUM DOLOR SIT</text><text x="1073" y="1019">LOREM IPSUM DOLOR SIT</text></g>
    </g>
  </g>

  <!-- ============ Panel 6 : receivables ============ -->
  <g class="receivables">
    <rect class="panel" x="1302" y="616" width="612" height="538"/>
    <text class="head-sm" x="1388" y="735">RECEIVABLES</text>
    <text class="lbl-sm" x="1492" y="733">SUB-PROCESS</text>
    <text class="lbl-sm" x="1637" y="733">DRIVERS</text>
    <text class="lbl-sm" x="1802" y="733">SUB-DRIVERS</text>
    <rect class="box-o" x="1346" y="849" width="84" height="44" stroke-width="1.5"/>
    <text class="lbl"><tspan x="1388" y="868">RECEIVABLES</tspan><tspan x="1388" y="880">DRIVERS</tspan></text>
    <path class="tree" stroke-width="1.2" d="M1430 871H1440M1440 775V985M1440 775H1450M1440 873H1450M1440 985H1450
      M1542 775H1550M1550 750V799M1550 750H1558M1550 775H1558M1550 799H1558
      M1542 873H1550M1550 849V898M1550 849H1558M1550 874H1558M1550 898H1558
      M1542 985H1550M1550 961V1010M1550 961H1558M1550 986H1558M1550 1010H1558
      M1702 799H1716M1716 788V855M1716 788H1733M1716 807H1733M1716 836H1733M1716 855H1733
      M1702 874H1716M1716 879V916M1716 879H1733M1716 898H1733M1716 916H1733M1716 868V879
      M1702 961H1716M1716 940V977M1716 940H1733M1716 959H1733M1716 977H1733
      M1702 1010H1716M1716 1001V1039M1716 1001H1733M1716 1020H1733M1716 1039H1733"/>
    <g fill="#fff" stroke="var(--orange)" stroke-width="1.3">
      <rect x="1450" y="767" width="92" height="17"/><rect x="1450" y="865" width="92" height="17"/><rect x="1450" y="977" width="92" height="17"/>
    </g>
    <g class="lbl-xs"><text x="1496" y="778">LOREM IPSUM</text><text x="1496" y="876">LOREM IPSUM</text><text x="1496" y="988">LOREM IPSUM</text></g>
    <g fill="#fff" stroke="var(--cyan)" stroke-width="1.2">
      <rect x="1575" y="742" width="127" height="16"/><rect x="1575" y="767" width="127" height="16"/><rect x="1575" y="791" width="127" height="16"/>
      <rect x="1575" y="841" width="127" height="16"/><rect x="1575" y="866" width="127" height="16"/><rect x="1575" y="890" width="127" height="16"/>
      <rect x="1575" y="953" width="127" height="16"/><rect x="1575" y="978" width="127" height="16"/><rect x="1575" y="1002" width="127" height="16"/>
    </g>
    <g fill="var(--orange)" stroke="#fff" stroke-width="1.5">
      <circle cx="1567" cy="750" r="10"/><circle cx="1567" cy="775" r="10"/><circle cx="1567" cy="799" r="10"/>
      <circle cx="1567" cy="849" r="10"/><circle cx="1567" cy="874" r="10"/><circle cx="1567" cy="898" r="10"/>
      <circle cx="1567" cy="961" r="10"/><circle cx="1567" cy="986" r="10"/><circle cx="1567" cy="1010" r="10"/>
    </g>
    <g class="w" font-size="10">
      <text x="1567" y="754">14</text><text x="1567" y="779">15</text><text x="1567" y="803">16</text>
      <text x="1567" y="853">14</text><text x="1567" y="878">15</text><text x="1567" y="902">16</text>
      <text x="1567" y="965">14</text><text x="1567" y="990">15</text><text x="1567" y="1014">16</text>
    </g>
    <g class="lbl-xs" font-size="5.5">
      <text x="1637" y="752">LOREM IPSUM DOLOR SIT</text><text x="1637" y="777">LOREM IPSUM DOLOR SIT</text><text x="1637" y="801">LOREM IPSUM DOLOR SIT</text>
      <text x="1637" y="851">LOREM IPSUM DOLOR SIT</text><text x="1637" y="876">LOREM IPSUM DOLOR SIT</text><text x="1637" y="900">LOREM IPSUM DOLOR SIT</text>
      <text x="1637" y="963">LOREM IPSUM DOLOR SIT</text><text x="1637" y="988">LOREM IPSUM DOLOR SIT</text><text x="1637" y="1012">LOREM IPSUM DOLOR SIT</text>
    </g>
    <g fill="#fff" stroke="var(--orange)" stroke-width="1.2">
      <rect x="1733" y="782" width="137" height="12"/><rect x="1733" y="801" width="137" height="12"/><rect x="1733" y="830" width="137" height="12"/>
      <rect x="1733" y="849" width="137" height="12"/><rect x="1733" y="873" width="137" height="12"/><rect x="1733" y="892" width="137" height="12"/>
      <rect x="1733" y="910" width="137" height="12"/><rect x="1733" y="934" width="137" height="12"/><rect x="1733" y="953" width="137" height="12"/>
      <rect x="1733" y="971" width="137" height="12"/><rect x="1733" y="995" width="137" height="12"/><rect x="1733" y="1014" width="137" height="12"/>
      <rect x="1733" y="1033" width="137" height="12"/>
    </g>
    <g class="lbl-xs">
      <text x="1802" y="790">LOREM IPSUM</text><text x="1802" y="809">LOREM IPSUM</text><text x="1802" y="838">LOREM IPSUM</text>
      <text x="1802" y="857">LOREM IPSUM</text><text x="1802" y="881">LOREM IPSUM</text><text x="1802" y="900">LOREM IPSUM</text>
      <text x="1802" y="918">LOREM IPSUM</text><text x="1802" y="942">LOREM IPSUM</text><text x="1802" y="961">LOREM IPSUM</text>
      <text x="1802" y="979">LOREM IPSUM</text><text x="1802" y="1003">LOREM IPSUM</text><text x="1802" y="1022">LOREM IPSUM</text>
      <text x="1802" y="1041">LOREM IPSUM</text>
    </g>
  </g>

  <!-- ============ Panel 7 : gears ============ -->
  <g class="gears">
    <rect class="panel" x="29" y="1184" width="612" height="538"/>
    <g fill="none" stroke="#1a3a8f" stroke-width="2.5" marker-end="url(#ahN)">
      <path d="M312 1228C380 1195 480 1220 500 1318"/>
      <path d="M165 1408C120 1480 150 1570 244 1596"/>
      <path d="M520 1535C535 1620 470 1690 376 1682"/>
    </g>
    <g>
      <circle cx="378" cy="1328" r="82" fill="none" stroke="var(--blue)" stroke-width="26" stroke-dasharray="24 40.4"/>
      <circle cx="378" cy="1328" r="76" fill="var(--blue)"/>
      <text class="w" font-size="15"><tspan x="378" y="1324">ACCOUNTS</tspan><tspan x="378" y="1343">RECEIVABLE</tspan></text>
    </g>
    <g>
      <circle cx="260" cy="1468" r="82" fill="none" stroke="var(--orange)" stroke-width="26" stroke-dasharray="24 40.4" transform="rotate(15 260 1468)"/>
      <circle cx="260" cy="1468" r="76" fill="var(--orange)"/>
      <text class="w" font-size="15" x="260" y="1474">INVENTORY</text>
    </g>
    <g>
      <circle cx="408" cy="1558" r="82" fill="none" stroke="var(--cyan)" stroke-width="26" stroke-dasharray="24 40.4" transform="rotate(8 408 1558)"/>
      <circle cx="408" cy="1558" r="76" fill="var(--cyan)"/>
      <text class="w" font-size="15"><tspan x="408" y="1554">ACCOUNTS</tspan><tspan x="408" y="1573">PAYABLE</tspan></text>
    </g>
  </g>

  <!-- ============ Panel 8 : hub ============ -->
  <g class="hub">
    <rect class="panel" x="664" y="1184" width="612" height="538"/>
    <g stroke="var(--navy)" stroke-width="3">
      <path d="M966 1320V1348M1047 1355L1036 1367M1098 1436L1074 1440M1084 1522L1060 1515M1004 1580L995 1556M928 1580L935 1556M848 1522L872 1515M834 1436L858 1440M885 1355L896 1367"/>
    </g>
    <circle cx="966" cy="1455" r="107" fill="none" stroke="var(--navy)" stroke-width="3"/>
    <g fill="var(--navy)">
      <circle cx="966" cy="1348" r="4"/><circle cx="1036" cy="1376" r="4"/><circle cx="1069" cy="1438" r="4"/>
      <circle cx="1056" cy="1511" r="4"/><circle cx="1001" cy="1556" r="4"/><circle cx="930" cy="1556" r="4"/>
      <circle cx="875" cy="1511" r="4"/><circle cx="862" cy="1438" r="4"/><circle cx="897" cy="1376" r="4"/>
    </g>
    <circle cx="966" cy="1455" r="90" fill="var(--cyan)"/>
    <text class="w" font-size="26" font-weight="800"><tspan x="966" y="1450">WORKING</tspan><tspan x="966" y="1482">CAPITALS</tspan></text>
    <g>
      <circle class="sat" cx="966" cy="1275" r="45"/><circle class="sat-arc" cx="966" cy="1275" r="45" stroke-dasharray="110 173" transform="rotate(-90 966 1275)"/>
      <circle class="sat" cx="1081" cy="1317" r="45"/><circle class="sat-arc" cx="1081" cy="1317" r="45" stroke-dasharray="110 173" transform="rotate(-60 1081 1317)"/>
      <circle class="sat" cx="1143" cy="1423" r="45"/><circle class="sat-arc" cx="1143" cy="1423" r="45" stroke-dasharray="110 173" transform="rotate(170 1143 1423)"/>
      <circle class="sat" cx="1122" cy="1545" r="45"/><circle class="sat-arc" cx="1122" cy="1545" r="45" stroke-dasharray="110 173" transform="rotate(90 1122 1545)"/>
      <circle class="sat" cx="1028" cy="1625" r="45"/><circle class="sat-arc" cx="1028" cy="1625" r="45" stroke-dasharray="110 173" transform="rotate(-40 1028 1625)"/>
      <circle class="sat" cx="905" cy="1625" r="45"/><circle class="sat-arc" cx="905" cy="1625" r="45" stroke-dasharray="110 173" transform="rotate(20 905 1625)"/>
      <circle class="sat" cx="810" cy="1545" r="45"/><circle class="sat-arc" cx="810" cy="1545" r="45" stroke-dasharray="110 173" transform="rotate(0 810 1545)"/>
      <circle class="sat" cx="789" cy="1423" r="45"/><circle class="sat-arc" cx="789" cy="1423" r="45" stroke-dasharray="110 173" transform="rotate(60 789 1423)"/>
      <circle class="sat" cx="850" cy="1317" r="45"/><circle class="sat-arc" cx="850" cy="1317" r="45" stroke-dasharray="110 173" transform="rotate(180 850 1317)"/>
    </g>
    <g class="head-sm" font-size="13">
      <text><tspan x="966" y="1273">LOREM</tspan><tspan x="966" y="1288">IPSUM</tspan></text>
      <text><tspan x="1081" y="1315">LOREM</tspan><tspan x="1081" y="1330">IPSUM</tspan></text>
      <text><tspan x="1143" y="1421">LOREM</tspan><tspan x="1143" y="1436">IPSUM</tspan></text>
      <text><tspan x="1122" y="1543">LOREM</tspan><tspan x="1122" y="1558">IPSUM</tspan></text>
      <text><tspan x="1028" y="1623">LOREM</tspan><tspan x="1028" y="1638">IPSUM</tspan></text>
      <text><tspan x="905" y="1623">LOREM</tspan><tspan x="905" y="1638">IPSUM</tspan></text>
      <text><tspan x="810" y="1543">LOREM</tspan><tspan x="810" y="1558">IPSUM</tspan></text>
      <text><tspan x="789" y="1421">LOREM</tspan><tspan x="789" y="1436">IPSUM</tspan></text>
      <text><tspan x="850" y="1315">LOREM</tspan><tspan x="850" y="1330">IPSUM</tspan></text>
    </g>
  </g>

  <!-- ============ Panel 9 : flow ============ -->
  <g class="flow">
    <rect class="panel" x="1302" y="1184" width="612" height="538"/>
    <g stroke="var(--blue)" stroke-width="1.2" fill="none">
      <path d="M1381 1406V1432M1487 1350V1358M1487 1406V1432M1566 1406V1416H1430V1432M1686 1406V1432M1769 1350V1358M1769 1406V1432M1838 1406V1432"/>
      <path d="M1487 1488V1509M1769 1488V1509M1838 1488V1509M1494 1488V1500H1712V1488M1545 1488V1500M1600 1488V1500M1655 1488V1500"/>
    </g>
    <g fill="var(--blue)">
      <path d="M1343 1432H1398L1408 1460L1398 1488H1343Z"/>
      <path d="M1400 1432H1455L1465 1460L1455 1488H1400L1410 1460Z"/>
      <path d="M1457 1432H1512L1522 1460L1512 1488H1457L1467 1460Z"/>
      <path d="M1514 1432H1571L1581 1460L1571 1488H1514L1524 1460Z"/>
      <path d="M1573 1432H1628L1638 1460L1628 1488H1573L1583 1460Z"/>
      <path d="M1630 1432H1685L1695 1460L1685 1488H1630L1640 1460Z"/>
      <path d="M1687 1432H1739L1749 1460L1739 1488H1687L1697 1460Z"/>
    </g>
    <g fill="#1f6fe0">
      <path d="M1741 1432H1796L1806 1460L1796 1488H1741L1751 1460Z"/>
      <path d="M1808 1432H1862L1872 1460L1862 1488H1808L1818 1460Z"/>
    </g>
    <g class="w" font-size="8">
      <text x="1375" y="1464">LOREM</text>
      <text><tspan x="1434" y="1458">LOREM</tspan><tspan x="1434" y="1468">IPSUM</tspan></text>
      <text><tspan x="1490" y="1458">LOREM</tspan><tspan x="1490" y="1468">IPSUM</tspan></text>
      <text x="1548" y="1464">LOREM</text>
      <text><tspan x="1608" y="1458">LOREM</tspan><tspan x="1608" y="1468">IPSUM</tspan></text>
      <text><tspan x="1664" y="1458">LOREM</tspan><tspan x="1664" y="1468">IPSUM</tspan></text>
      <text><tspan x="1718" y="1458">LOREM</tspan><tspan x="1718" y="1468">IPSUM</tspan></text>
      <text><tspan x="1774" y="1458">LOREM</tspan><tspan x="1774" y="1468">IPSUM</tspan></text>
      <text><tspan x="1841" y="1458">LOREM</tspan><tspan x="1841" y="1468">IPSUM</tspan></text>
    </g>
    <g fill="var(--orange)">
      <rect x="1343" y="1358" width="77" height="48"/><rect x="1527" y="1358" width="77" height="48"/><rect x="1648" y="1358" width="77" height="48"/>
    </g>
    <g fill="var(--cyan)">
      <rect x="1454" y="1302" width="66" height="48"/><rect x="1454" y="1358" width="66" height="48"/>
      <rect x="1736" y="1302" width="66" height="48"/><rect x="1736" y="1358" width="66" height="48"/><rect x="1806" y="1358" width="64" height="48"/>
      <rect x="1454" y="1509" width="66" height="48"/><rect x="1734" y="1509" width="66" height="48"/><rect x="1806" y="1509" width="64" height="48"/>
    </g>
    <g class="w" font-size="8">
      <text><tspan x="1381" y="1380">LOREM</tspan><tspan x="1381" y="1390">IPSUM</tspan></text>
      <text><tspan x="1566" y="1380">LOREM</tspan><tspan x="1566" y="1390">IPSUM</tspan></text>
      <text><tspan x="1686" y="1380">LOREM</tspan><tspan x="1686" y="1390">IPSUM</tspan></text>
      <text><tspan x="1487" y="1324">LOREM</tspan><tspan x="1487" y="1334">IPSUM</tspan></text>
      <text><tspan x="1487" y="1380">LOREM</tspan><tspan x="1487" y="1390">IPSUM</tspan></text>
      <text><tspan x="1769" y="1324">LOREM</tspan><tspan x="1769" y="1334">IPSUM</tspan></text>
      <text><tspan x="1769" y="1380">LOREM</tspan><tspan x="1769" y="1390">IPSUM</tspan></text>
      <text><tspan x="1838" y="1380">LOREM</tspan><tspan x="1838" y="1390">IPSUM</tspan></text>
      <text><tspan x="1487" y="1531">LOREM</tspan><tspan x="1487" y="1541">IPSUM</tspan></text>
      <text><tspan x="1767" y="1531">LOREM</tspan><tspan x="1767" y="1541">IPSUM</tspan></text>
      <text><tspan x="1838" y="1531">LOREM</tspan><tspan x="1838" y="1541">IPSUM</tspan></text>
    </g>
    <g class="legend">
      <rect x="1585" y="1585" width="11" height="11" fill="var(--blue)"/>
      <text class="legend-text" x="1599" y="1594">INVENTORY</text>
      <rect x="1652" y="1585" width="11" height="11" fill="var(--orange)"/>
      <text class="legend-text"><tspan x="1667" y="1592">PAYABLES AND</tspan><tspan x="1667" y="1601">PREPAYMENTS MADE</tspan></text>
      <rect x="1758" y="1585" width="11" height="11" fill="var(--cyan)"/>
      <text class="legend-text"><tspan x="1773" y="1592">RECEIVABLES AND</tspan><tspan x="1773" y="1601">PREPAYMENTS RECEIVED</tspan></text>
    </g>
  </g>
</svg>
</body>
</html>
```